Accounting firm needing business card / letterhead designed
Marcus L. Trenholm, CPA
marcus@veltrowledger.com
www.veltrowledger.com
842 E Alder Ave Harwick Falls, MN 43827
419-562-0974

```html
<!DOCTYPE html>
<html lang="en">
<head>
<meta charset="utf-8">
<title>Veltrow Ledger – Business Card</title>
<link href="https://fonts.googleapis.com/css2?family=Oswald:wght@600&family=Mulish:wght@400;600&display=swap" rel="stylesheet">
<style>
  :root {
    --bg: #262626;
    --card: #1e1e1e;
    --card-edge: #2b2b2b;
    --green: #7cc242;
    --text: #e8e8e8;
    --logo-grey: #8d8d8d;
  }
  * { margin: 0; padding: 0; box-sizing: border-box; }
  html, body { width: 1200px; height: 900px; overflow: hidden; background: var(--bg); }
  .canvas {
    width: 1200px; height: 900px; position: relative;
    font-family: "Mulish", sans-serif; color: var(--text);
  }
  .card {
    position: absolute; left: 240px; width: 720px; height: 411px;
    background: linear-gradient(135deg, var(--card) 0%, var(--card) 55%, var(--card-edge) 100%);
    box-shadow: 0 10px 30px rgba(0,0,0,.45);
  }
  .card--front { top: 26px; }
  .card--back { top: 463px; }

  .brand {
    position: absolute; left: 0; right: 0; top: 160px; text-align: center;
    font-size: 46px; font-weight: 600; letter-spacing: 4px;
    color: var(--logo-grey); text-transform: uppercase; white-space: nowrap;
  }
  .front-web {
    position: absolute; left: 0; right: 0; bottom: 44px; text-align: center;
    font-size: 16px; letter-spacing: 1px;
  }
  .accent { color: var(--green); }

  .identity {
    position: absolute; right: 370px; top: 138px; text-align: right; white-space: nowrap;
  }
  .identity__name {
    font-family: "Oswald", sans-serif; font-weight: 600; font-size: 36px;
    color: var(--green); text-transform: uppercase; letter-spacing: 1px; line-height: 1.1;
  }
  .identity__title { font-size: 18px; margin-top: 4px; }
  .divider {
    position: absolute; left: 370px; top: 145px; width: 2px; height: 70px;
    background: var(--green);
  }
  .contact {
    position: absolute; left: 392px; top: 142px; list-style: none;
    font-size: 18px; letter-spacing: .5px; white-space: nowrap;
  }
  .contact li { display: flex; align-items: center; height: 25px; }
  .contact svg { width: 16px; height: 16px; margin-right: 14px; flex: none; }
  .address {
    position: absolute; left: 0; right: 0; bottom: 52px; text-align: center;
    font-size: 18px; letter-spacing: .5px; white-space: nowrap;
  }
</style>
</head>
<body>
<main class="canvas">
  <section class="card card--front">
    <div class="brand">Veltrow Ledger</div>
    <div class="front-web">www.<span class="accent">veltrowledger</span>.com</div>
  </section>

  <section class="card card--back">
    <div class="identity">
      <div class="identity__name">Marcus L. Trenholm</div>
      <div class="identity__title">CPA</div>
    </div>
    <div class="divider"></div>
    <ul class="contact">
      <li>
        <svg viewBox="0 0 16 16" aria-hidden="true"><rect x="4" y="1" width="8" height="14" rx="1.5" fill="none" stroke="#7cc242" stroke-width="1.5"/><line x1="6.5" y1="12.5" x2="9.5" y2="12.5" stroke="#7cc242" stroke-width="1.2"/></svg>
        555-562-0974
      </li>
      <li>
        <svg viewBox="0 0 16 16" aria-hidden="true"><rect x="1" y="3" width="14" height="10" fill="#7cc242"/><polyline points="1,3 8,9 15,3" fill="none" stroke="#1e1e1e" stroke-width="1.3"/></svg>
        marcus@veltrowledger.com
      </li>
      <li>
        <svg viewBox="0 0 16 16" aria-hidden="true"><g fill="none" stroke="#7cc242" stroke-width="1.2"><circle cx="8" cy="8" r="6.5"/><ellipse cx="8" cy="8" rx="3" ry="6.5"/><line x1="1.5" y1="8" x2="14.5" y2="8"/><line x1="2.5" y1="4.5" x2="13.5" y2="4.5"/><line x1="2.5" y1="11.5" x2="13.5" y2="11.5"/></g></svg>
        www.<span class="accent">veltrowledger</span>.com
      </li>
    </ul>
    <div class="address">842 E Alder Ave Harwick Falls, MN 43827</div>
  </section>
</main>
</body>
</html>
```